Brimlow OrthoLink IT Inc. new website

i need a website for my company which is dedicated to installation and service of computer systems in Dental Offices. I would like for it to encompass a technology feel and professional look. The company deals with all aspects of technology like, Audio Visual, computer systems and networks, Cloud services like data backup, data center. We provide manage services, support and services to Dental Professionals.
Updates

Looking for a Technology font but professional look Added Wednesday, April 20, 2016

Target Market(s)

Dental, Dentist

Industry/Entity Type

Dental

Number of Pages Required

5+ page

Font styles to use
Other font styles liked:
• Futuristic or Techy

Colors
0255a3
ec1f27

Requirements
Must have
• Tabs
Nice to have
• Have no idea maybe some suggestion on your part may help
Should not have
• A professional feel but have a techy look

```html
<!DOCTYPE html>
<html lang="en">
<head>
<meta charset="utf-8">
<title>Brimlow OrthoLink IT Inc.</title>
<link rel="stylesheet" href="https://fonts.googleapis.com/css2?family=Open+Sans:wght@300;400;600;700&display=swap">
<style>
:root{
  --brand-blue:#0255a3;
  --brand-red:#ec1f27;
  --sky-top:#2aa3ea;
  --sky-bottom:#0b7ad4;
  --ink:#333;
  --muted:#666;
  --soft-bg:#efefef;
  --form-bg:#e8e8e8;
  --footer:#333333;
  --footer-line:#474747;
  --footer-text:#d9d9d9;
  --white:#fff;
}
*{box-sizing:border-box;margin:0;padding:0}
html,body{width:1200px;height:2575px;overflow:hidden}
body{font-family:"Open Sans",Arial,sans-serif;color:var(--ink);background:var(--white);position:relative}
.section{position:absolute;left:0;width:1200px}

/* header */
.site-header{top:0;height:96px;background:var(--white)}
.brand{position:absolute;left:132px;top:30px;display:flex;align-items:center;gap:10px;font-weight:700;font-size:24px;color:var(--brand-blue);letter-spacing:-.3px}
.brand-square{width:14px;height:14px;background:var(--brand-blue)}
.main-nav{position:absolute;right:134px;top:40px;display:flex;gap:28px;font-size:11.5px;font-weight:600;text-transform:uppercase;color:#222}
.main-nav .active{color:var(--brand-red)}

/* hero */
.hero{top:96px;height:518px}
.hero-media{position:absolute;inset:0;background:linear-gradient(100deg,#e9eef3 0%,#c9d3dd 35%,#9fb1c4 60%,#1f2a38 85%,#2b3542 100%)}
.hero-dots{position:absolute;left:572px;top:486px;display:flex;gap:8px}
.hero-dots span{width:7px;height:7px;border-radius:50%;background:rgba(255,255,255,.55)}
.hero-dots span:first-child{background:var(--white)}

/* services */
.services{top:614px;height:359px;background:linear-gradient(180deg,var(--sky-top),var(--sky-bottom));color:var(--white)}
.services-title{position:absolute;left:195px;top:30px;font-size:40px;font-weight:300}
.services-art{position:absolute;left:132px;top:98px;width:305px;height:236px;border-radius:6px;background:radial-gradient(circle at 30% 70%,#cfe6fb 0%,#5aa8e6 35%,rgba(20,100,180,.2) 70%,transparent 100%)}
.service-list{position:absolute;left:495px;top:36px;width:571px}
.service-item{display:flex;gap:14px;height:104px}
.service-icon{flex:none;width:64px;height:64px;border:1.5px solid rgba(255,255,255,.8);border-radius:50%;display:flex;align-items:center;justify-content:center}
.service-item h3{font-size:21px;font-weight:400;margin-top:6px}
.service-item p{font-size:9.5px;line-height:15px;opacity:.9;margin-top:3px;max-width:490px}

/* about */
.about{top:973px;height:255px;text-align:center}
.about h2{margin-top:46px;font-size:39px;font-weight:300;color:var(--brand-red)}
.about p{width:940px;margin:12px auto 0;font-size:10px;line-height:19px;color:var(--muted)}
.offer-row{margin-top:18px;display:flex;justify-content:center;gap:54px;font-size:15px;color:var(--brand-red)}
.offer-row span{display:flex;align-items:center;gap:8px}

/* works */
.works{top:1228px;height:275px;background:var(--soft-bg)}
.works h2{position:absolute;left:132px;top:24px;font-size:24px;font-weight:400;color:var(--brand-blue)}
.works-arrows{position:absolute;left:1036px;top:34px;display:flex;gap:6px}
.works-arrows span{width:13px;height:13px;background:var(--white);border-radius:2px;display:flex;align-items:center;justify-content:center}
.works-grid{position:absolute;left:132px;top:76px;display:flex;gap:3px}
.work-tile{width:232px;height:158px}
.tile-1{background:linear-gradient(135deg,#e6e1dc,#8a7e74)}
.tile-2{background:linear-gradient(135deg,#e9eff4,#7ea1bd)}
.tile-3{background:linear-gradient(135deg,#c8ced3,#5b6670)}
.tile-4{background:linear-gradient(135deg,#5a4a33,#c9b68d)}

/* testimonial */
.testimonial{top:1503px;height:340px;text-align:center}
.avatar{position:absolute;left:557px;top:34px;width:86px;height:86px;border-radius:50%;background:radial-gradient(circle,#efe6df,#b9a89b)}
.quote{position:absolute;left:170px;top:140px;width:860px;font-size:27px;font-weight:300;line-height:40px;color:#8a8a8a}
.quote-mark{font-weight:700;color:#9a9a9a;font-size:34px;vertical-align:-4px}
.quote-author{position:absolute;left:0;top:232px;width:1200px;font-size:15px;color:#222}
.testimonial-dots{position:absolute;left:570px;top:289px;display:flex;gap:8px}
.testimonial-dots span{width:7px;height:7px;border-radius:50%;background:#999}
.testimonial-dots span:first-child{background:#2aa3c7}

/* quote form */
.quick-quote{top:1843px;height:303px;background:var(--form-bg)}
.quick-quote h2{position:absolute;left:0;top:28px;width:1200px;text-align:center;font-size:38px;font-weight:300;color:var(--brand-blue)}
.field{position:absolute;height:40px;background:var(--white);font-size:10px;color:#555;padding:14px 16px}
.field-select::after{content:"\2195";position:absolute;right:14px;top:11px;font-size:11px;color:#777}
.submit{position:absolute;left:555px;top:224px;width:90px;height:39px;background:#3a3a3a;color:var(--white);font-size:11px;display:flex;align-items:center;justify-content:center}

/* map */
.map{top:2146px;height:245px;background:linear-gradient(180deg,#e7e7e7,#d8d8d8)}

/* footer */
.footer-contact{top:2391px;height:83px;background:var(--footer);color:var(--footer-text);font-size:11px}
.contact-item{position:absolute;top:34px;display:flex;align-items:center;gap:8px}
.footer-bottom{top:2474px;height:101px;background:var(--footer);border-top:1px solid var(--footer-line);color:var(--footer-text);font-size:9.5px}
.footer-links{position:absolute;left:132px;top:30px}
.copyright{position:absolute;left:132px;top:56px}
.social{position:absolute;left:975px;top:36px;display:flex;gap:8px}
.social span{width:25px;height:25px;border-radius:50%;background:#2b6cb3}
</style>
</head>
<body>

<header class="section site-header">
  <div class="brand"><span class="brand-square"></span>Brimlow OrthoLink IT</div>
  <nav class="main-nav">
    <span class="active">Home</span><span>Services</span><span>Products</span><span>Testimonials</span><span>About Us</span><span>Contact Us</span>
  </nav>
</header>

<section class="section hero">
  <div class="hero-media" role="img" aria-label="Photo of a dental IT technician in a blue shirt beside a monitor showing dental imaging software"></div>
  <div class="hero-dots"><span></span><span></span><span></span><span></span></div>
</section>

<section class="section services">
  <h2 class="services-title">Our Services</h2>
  <div class="services-art" role="img" aria-label="Illustration of a computer monitor beside a glowing network globe"></div>
  <div class="service-list">
    <div class="service-item">
      <div class="service-icon"><svg width="24" height="24" viewBox="0 0 24 24" fill="none" stroke="#fff" stroke-width="2"><path d="M4 9h4l5-4v14l-5-4H4z" fill="#fff"/><path d="M16 9a4 4 0 0 1 0 6M18.5 6.5a7.5 7.5 0 0 1 0 11"/></svg></div>
      <div><h3>Audio Visual</h3><p>Conference screens, sound and displays set up for waiting rooms and operatories. Clean wiring, tested and ready for daily patient use.</p></div>
    </div>
    <div class="service-item">
      <div class="service-icon"><svg width="24" height="24" viewBox="0 0 24 24" fill="#fff" stroke="#fff" stroke-width="1.6"><rect x="9" y="3" width="6" height="5"/><rect x="3" y="16" width="6" height="5"/><rect x="15" y="16" width="6" height="5"/><path d="M12 8v4M6 16v-4h12v4" fill="none"/></svg></div>
      <div><h3>Computer Systems and Networks</h3><p>Workstations, servers and secure networks built for imaging and practice software. We plan, install and keep every device running well.</p></div>
    </div>
    <div class="service-item">
      <div class="service-icon"><svg width="24" height="24" viewBox="0 0 24 24" fill="none" stroke="#fff" stroke-width="2"><path d="M5 6h14l2 8v4H3v-4z"/><path d="M3 14h18"/><circle cx="17" cy="16" r=".8" fill="#fff"/></svg></div>
      <div><h3>Cloud Services of Data Backup</h3><p>Encrypted offsite backup and data center hosting for patient records. Files restored fast, so your office never stops seeing patients.</p></div>
    </div>
  </div>
</section>

<section class="section about">
  <h2>About Brimlow OrthoLink IT</h2>
  <p>We help dental offices run on technology that simply works. From the first network cable to the last backup check, our team plans, installs and supports the systems your practice depends on every day. We know imaging software, chairside displays and secure patient records, and we answer the phone when something goes wrong. Our goal is steady, quiet technology so your staff can focus on care, not computers. Local engineers, clear pricing and fast response times come standard with every plan.</p>
  <div class="offer-row">
    <span>We provide...</span>
    <span><svg width="14" height="14" viewBox="0 0 24 24" fill="var(--brand-red)"><path d="M21 6a5 5 0 0 1-7 5L5 20l-2-2 9-9a5 5 0 0 1 5-7l-3 3 1 3 3 1z"/></svg>Manage Services</span>
    <span><svg width="14" height="14" viewBox="0 0 24 24" fill="none" stroke="var(--brand-red)" stroke-width="3"><circle cx="12" cy="12" r="9"/><circle cx="12" cy="12" r="4"/></svg>Support</span>
    <span><svg width="14" height="14" viewBox="0 0 24 24" fill="var(--brand-red)"><circle cx="12" cy="12" r="7"/><path d="M11 1h2v5h-2zM11 18h2v5h-2zM1 11h5v2H1zM18 11h5v2h-5z"/><circle cx="12" cy="12" r="3" fill="#fff"/></svg>Service to Dental Professionals</span>
  </div>
</section>

<section class="section works">
  <h2>Our Works</h2>
  <div class="works-arrows">
    <span><svg width="6" height="8" viewBox="0 0 6 8"><path d="M5 0 1 4l4 4" fill="none" stroke="#555"/></svg></span>
    <span><svg width="6" height="8" viewBox="0 0 6 8"><path d="M1 0l4 4-4 4" fill="none" stroke="#555"/></svg></span>
  </div>
  <div class="works-grid">
    <div class="work-tile tile-1" role="img" aria-label="Photo of a staff member working at a computer in a dental office"></div>
    <div class="work-tile tile-2" role="img" aria-label="Photo of a dental assistant in a bright treatment room"></div>
    <div class="work-tile tile-3" role="img" aria-label="Photo of an intraoral scanner in use during treatment"></div>
    <div class="work-tile tile-4" role="img" aria-label="Photo of a dentist holding a tablet showing an x-ray"></div>
  </div>
</section>

<section class="section testimonial">
  <div class="avatar" role="img" aria-label="Portrait of the client giving the testimonial"></div>
  <p class="quote"><span class="quote-mark">&ldquo;</span> Praesent porta tortor dolor, quis maximus tortor pretium et. Praesent eget vulputate risus. Suspendisse dignissim. <span class="quote-mark">&rdquo;</span></p>
  <p class="quote-author">- Mara Keel, City</p>
  <div class="testimonial-dots"><span></span><span></span><span></span><span></span></div>
</section>

<section class="section quick-quote">
  <h2>Get a Quick Quote</h2>
  <div class="field" style="left:145px;top:98px;width:209px">Name</div>
  <div class="field" style="left:379px;top:98px;width:209px">Email</div>
  <div class="field" style="left:612px;top:98px;width:209px">Phone</div>
  <div class="field field-select" style="left:846px;top:98px;width:209px">Service for</div>
  <div class="field" style="left:145px;top:161px;width:910px">Messages</div>
  <div class="submit">SUBMIT</div>
</section>

<section class="section map" role="img" aria-label="Light grey world map"></section>

<section class="section footer-contact">
  <div class="contact-item" style="left:132px"><svg width="10" height="13" viewBox="0 0 10 13" fill="#ddd"><path d="M5 0a5 5 0 0 1 5 5c0 3-5 8-5 8S0 8 0 5a5 5 0 0 1 5-5z"/><circle cx="5" cy="5" r="2" fill="#333"/></svg>24 Building name, Street name, City - Zipcode</div>
  <div class="contact-item" style="left:460px"><svg width="12" height="12" viewBox="0 0 24 24" fill="#ddd"><path d="M6 2l4 5-2 3a12 12 0 0 0 6 6l3-2 5 4-3 4C10 22 2 14 2 5z"/></svg>Phone : (555) 014 2270</div>
  <div class="contact-item" style="left:672px"><svg width="13" height="12" viewBox="0 0 26 24" fill="#ddd"><rect x="6" y="0" width="14" height="7"/><rect x="0" y="8" width="26" height="12" rx="2"/><rect x="6" y="16" width="14" height="8" fill="#fff"/></svg>Fax : (555) 014 2270</div>
  <div class="contact-item" style="left:892px"><svg width="14" height="10" viewBox="0 0 14 10" fill="#ddd"><rect width="14" height="10"/><path d="M0 0l7 5 7-5" fill="none" stroke="#333"/></svg>Email: info@brimlowortholink.com</div>
</section>

<footer class="section footer-bottom">
  <div class="footer-links">Home &nbsp;|&nbsp; Services &nbsp;|&nbsp; Products &nbsp;|&nbsp; Testimonials &nbsp;|&nbsp; About us &nbsp;|&nbsp; Contact us</div>
  <div class="copyright">Copyright &copy; 2016 Brimlow OrthoLink IT Inc. &nbsp;All rights reserved.</div>
  <div class="social"><span></span><span></span><span></span></div>
</footer>

</body>
</html>
```